Brookvale Estates LLC stationary for a real estate property management company.

Create stationary (letterhead, envelopes, business cards) using Brookvale Estates LLC logo as primary creative element. Stationary design needs to be horizontal, leaving as much space as possible for correspondence copy. See attached Creative Brief and past stationary files for details.

Target Market(s)

Prospective apartment residents and current residents, vendors, and government agencies.

Industry/Entity Type

Property Management

Contact Information for Business Card

Business card employee title: Property Manager. Should include address, phone, fax, email, website, slogan, and Brookvale Estates logo.

Font styles to use
Sans Serif

Colors
0592cd
000000

Requirements
Must have
• Tone should be conservative, institutional, business (i.e. banking, finance, real estate). Must include: address, phone, fax, website, and slogan (see attached Creative Brief). Should be a horizontal design, leaving as much room as possible for letter correspondence copy.
Nice to have
• Please use an Arial or Helvetica style font.
Should not have
• Letterhead layout should leave as much room as possible for copy.

```html
<!DOCTYPE html>
<html lang="en">
<head>
<meta charset="utf-8">
<title>Brookvale Estates LLC – Business Card</title>
<link href="https://fonts.googleapis.com/css2?family=Arimo:wght@400;700&display=swap" rel="stylesheet">
<style>
  :root {
    --brand-blue: #0592cd;
    --deep-blue: #0a5f98;
    --sky-blue: #17b5e8;
    --name-blue: #1170b0;
    --charcoal: #3d3d3d;
    --text-grey: #4a4a4a;
    --paper: #f7f7f7;
    --backdrop: #2a2a2a;
    --white: #ffffff;
  }
  * { margin: 0; padding: 0; box-sizing: border-box; }
  html, body {
    width: 1200px; height: 960px; overflow: hidden;
    background: var(--backdrop);
    font-family: "Arimo", Arial, Helvetica, sans-serif;
  }
  .canvas { position: relative; width: 1200px; height: 960px; }

  .card { position: absolute; width: 600px; height: 342px; overflow: hidden; }
  .card-front { left: 302px; top: 129px; background: var(--paper); }
  .card-back {
    left: 299px; top: 488px;
    background: linear-gradient(135deg, var(--sky-blue) 0%, var(--brand-blue) 40%, var(--deep-blue) 100%);
  }

  .brand-lockup {
    position: absolute; left: 50px; top: 138px;
    display: flex; align-items: center; gap: 10px;
  }
  .brand-square { width: 26px; height: 26px; background: var(--brand-blue); }
  .brand-name {
    color: var(--brand-blue); font-weight: 700; font-size: 19px;
    line-height: 1.15; letter-spacing: 0.5px; text-transform: uppercase;
  }

  .divider {
    position: absolute; left: 307px; top: 70px; width: 1px; height: 178px;
    background: #c9c9c9;
  }

  .contact { position: absolute; left: 330px; top: 72px; color: var(--text-grey); }
  .contact-name { color: var(--name-blue); font-weight: 700; font-size: 20px; line-height: 24px; }
  .contact-title { font-size: 15px; line-height: 20px; margin-bottom: 8px; }
  .contact-address { font-size: 14px; line-height: 18px; margin-bottom: 8px; }
  .contact-list { list-style: none; font-size: 14px; }
  .contact-list li { display: flex; align-items: center; gap: 8px; height: 19px; }
  .contact-list svg { width: 14px; height: 14px; flex: none; }

  .wave { position: absolute; left: 0; bottom: 0; width: 600px; height: 60px; }

  .back-brand {
    position: absolute; left: 0; right: 0; top: 126px;
    text-align: center; color: var(--white);
    font-weight: 700; font-size: 30px; letter-spacing: 1px; text-transform: uppercase;
  }
  .slogan {
    position: absolute; left: 0; right: 0; top: 288px;
    text-align: center; color: var(--white); font-weight: 700; font-size: 17px;
  }
</style>
</head>
<body>
<main class="canvas">

  <section class="card card-front">
    <div class="brand-lockup">
      <span class="brand-square"></span>
      <div class="brand-name">Brookvale<br>Estates LLC</div>
    </div>

    <div class="divider"></div>

    <div class="contact">
      <div class="contact-name">DANIEL HARTLEY</div>
      <div class="contact-title">Property Manager</div>
      <div class="contact-address">2750 Alder Creek Road #B210<br>San Diego, CA 92118</div>
      <ul class="contact-list">
        <li>
          <svg viewBox="0 0 14 14"><path fill="#1170b0" d="M3 1l2.2 2.6-1.2 1.6c.8 1.8 2 3 3.8 3.8l1.6-1.2L12 10l-1.4 2.4C6 12.2 1.8 8 1.6 3.4z"/></svg>
          619-555-0142
        </li>
        <li>
          <svg viewBox="0 0 14 14"><rect x="4" y="1" width="6" height="4" fill="#1170b0"/><rect x="1" y="5" width="12" height="6" rx="1" fill="#1170b0"/><rect x="4" y="9" width="6" height="4" fill="#fff" stroke="#1170b0"/></svg>
          619-555-0187
        </li>
        <li>
          <svg viewBox="0 0 14 14"><rect x="1" y="3" width="12" height="8" fill="#1170b0"/><path d="M1.5 3.5L7 8l5.5-4.5" fill="none" stroke="#fff" stroke-width="1"/></svg>
          daniel@brookvaleestates.us
        </li>
        <li>
          <svg viewBox="0 0 14 14"><circle cx="7" cy="7" r="6" fill="#1170b0"/><path d="M4 4.5c1.5 0 2 1 1.5 2s1 2 .5 3.5M9 3c-.5 1 .5 1.5 1.5 1.5M8.5 11c0-1.5 1.5-1.5 2-3" fill="none" stroke="#fff" stroke-width="1"/></svg>
          www.brookvaleestates.us
        </li>
      </ul>
    </div>

    <svg class="wave" viewBox="0 0 600 60" preserveAspectRatio="none">
      <path fill="#0a72b5" d="M0 22 C150 40 300 30 420 22 C500 16 560 24 600 38 L600 60 L0 60 Z"/>
      <path fill="#ffffff" d="M0 20 C150 38 300 28 420 20 C500 14 560 22 600 36 L600 40 C560 27 500 19 420 25 C300 33 150 43 0 25 Z"/>
      <path fill="#3d3d3d" d="M0 2 C100 12 200 22 310 26 C200 26 100 22 0 16 Z"/>
      <path fill="#3d3d3d" d="M300 24 C400 14 480 6 540 8 C570 9 590 14 600 18 L600 30 C580 22 550 18 510 18 C430 18 360 22 300 24 Z"/>
    </svg>
  </section>

  <section class="card card-back">
    <div class="back-brand">Brookvale Estates LLC</div>
    <div class="slogan">Multifamily Property Management</div>
  </section>

</main>
</body>
</html>
```